Vantiqo custom business card design

Need a authentic, innovative business card design for a new mobile app business. I am uploading a few screen images from our app for you to view. I would like app design theme to match business card design. I can also send logo images.

```html
<!DOCTYPE html>
<html lang="en">
<head>
<meta charset="utf-8">
<title>Vantiqo business card</title>
<link rel="stylesheet" href="https://fonts.googleapis.com/css2?family=Montserrat:wght@700;800&family=Lato:wght@400&display=swap">
<style>
  :root {
    --stage: #676767;
    --paper: #ffffff;
    --purple: #5f0a87;
    --ink: #1e1e1e;
    --rule: #d6d6d6;
  }
  html, body {
    margin: 0;
    padding: 0;
    width: 1200px;
    height: 802px;
    overflow: hidden;
    background: var(--stage);
  }
  .canvas {
    position: relative;
    width: 1200px;
    height: 802px;
  }
  .card {
    position: absolute;
    top: 274px;
    width: 443px;
    height: 264px;
    box-shadow: 0 3px 8px rgba(0,0,0,0.45);
    overflow: hidden;
  }
  .card--front {
    left: 136px;
    background: var(--paper);
  }
  .card--back {
    left: 624px;
    background: linear-gradient(to right, var(--purple) 0 50%, var(--ink) 50% 100%);
  }
  .brand {
    position: absolute;
    left: 38px;
    width: 150px;
    top: 59px;
    display: flex;
    flex-direction: column;
    align-items: center;
    gap: 10px;
  }
  .brand__dot {
    width: 108px;
    height: 108px;
    border-radius: 50%;
    background: var(--purple);
  }
  .brand__name {
    font-family: "Montserrat", sans-serif;
    font-weight: 800;
    font-size: 29px;
    line-height: 1;
    color: var(--ink);
  }
  .divider {
    position: absolute;
    left: 202px;
    top: 69px;
    width: 1px;
    height: 134px;
    background: var(--rule);
  }
  .contact {
    position: absolute;
    left: 225px;
    top: 66px;
    font-family: "Lato", sans-serif;
    color: var(--ink);
  }
  .contact__name {
    margin: 0;
    font-family: "Montserrat", sans-serif;
    font-weight: 700;
    font-size: 17px;
    line-height: 19px;
    color: var(--purple);
  }
  .contact__role {
    margin: 0 0 6px;
    font-size: 12.5px;
    line-height: 14px;
  }
  .contact__list {
    list-style: none;
    margin: 0 0 6px;
    padding: 0;
  }
  .contact__item {
    display: flex;
    align-items: center;
    gap: 4px;
    font-size: 12.5px;
    line-height: 16px;
  }
  .contact__icon {
    width: 10px;
    height: 10px;
    fill: var(--purple);
    flex: none;
  }
  .contact__address {
    margin: 0;
    font-style: normal;
    font-size: 12.5px;
    line-height: 15.5px;
  }
  .back__name {
    position: absolute;
    inset: 0;
    display: flex;
    align-items: center;
    justify-content: center;
    font-family: "Montserrat", sans-serif;
    font-weight: 800;
    font-size: 46px;
    color: var(--paper);
  }
</style>
</head>
<body>
<main class="canvas">
  <section class="card card--front">
    <div class="brand">
      <span class="brand__dot"></span>
      <span class="brand__name">Vantiqo</span>
    </div>
    <div class="divider"></div>
    <div class="contact">
      <h1 class="contact__name">MARCUS ELLERY</h1>
      <p class="contact__role">Managing Director</p>
      <ul class="contact__list">
        <li class="contact__item">
          <svg class="contact__icon" viewBox="0 0 10 10"><path d="M1 3.5C1 2 2.5 1 5 1s4 1 4 2.5L7.5 4 7 3H3L2.5 4zM2.5 5h5L9 9H1z"/></svg>
          021-555 873 410
        </li>
        <li class="contact__item">
          <svg class="contact__icon" viewBox="0 0 10 10"><path d="M2.5 0h5v10h-5zM3.5 1v7h3V1z" fill-rule="evenodd"/></svg>
          021-555 873 411
        </li>
        <li class="contact__item">
          <svg class="contact__icon" viewBox="0 0 10 10"><path d="M0 2h10v6H0zM1 3l4 3 4-3z" fill-rule="evenodd"/></svg>
          info@vantiqo.app
        </li>
        <li class="contact__item">
          <svg class="contact__icon" viewBox="0 0 10 10"><circle cx="5" cy="5" r="4.5"/></svg>
          www.vantiqo.app
        </li>
      </ul>
      <address class="contact__address">48 Marlow Street, Suite 9<br>Harbourton, 560218.</address>
    </div>
  </section>

  <section class="card card--back">
    <div class="back__name">Vantiqo</div>
  </section>
</main>
</body>
</html>
```